Business Card for a Jewellery Brand

Business card for an upscale jewellery brand. Attached is the brand logo and icon and color board. I am looking for two card versions: one for the founder and one is generic. The card should be elegant and convey upscale and premium feel. I am open to both square and rectangle card shapes.

Industry/Entity Type

Jewelry

Contact Information for Business Card

Two cards: (1) Sunela Parvaniya (Founder) (2) General
(1) Sunela Parvaniya card should have Name: Sunela Parvaniya, Title: Founder Email id: sunela@quiremo.com.au. Phone no: +61452913307
(2) Generic card should have Email id: info@quiremo.com.au. Phone no: +61436207518

Requirements
Must have
• Workmark
• ICON
• Phone no
• Email ID
• ABN: 58219740312 (Note: ABN is Business number in Australia)
• Website: www.quiremo.com.au
• Instagram: quiremo_jewellery
• Facebook: @quiremojewellery
Nice to have
• Tagline

```html
<!DOCTYPE html>
<html lang="en">
<head>
<meta charset="utf-8">
<title>Quiremo Business Cards</title>
<link href="https://fonts.googleapis.com/css2?family=Raleway:wght@300;400;500&display=swap" rel="stylesheet">
<style>
  :root {
    --page: #ffffff;
    --marble-light: #f6f7f8;
    --marble-mid: #eceff1;
    --marble-dark: #e3e7ea;
    --copper: #b9755a;
    --blush: #e3918a;
    --grey: #9b9b9b;
  }
  html, body {
    margin: 0;
    padding: 0;
    width: 1200px;
    height: 738px;
    overflow: hidden;
    background: var(--page);
    font-family: "Raleway", sans-serif;
  }
  .canvas {
    position: relative;
    width: 1200px;
    height: 738px;
  }
  .card {
    position: absolute;
    top: 138px;
    width: 465px;
    height: 462px;
    overflow: hidden;
  }
  .card--generic { left: 92px; }
  .card--founder { left: 643px; }
  .marble {
    position: absolute;
    inset: 0;
    background: linear-gradient(135deg, var(--marble-light) 0%, var(--marble-mid) 45%, var(--marble-light) 70%, var(--marble-dark) 100%);
  }
  .centered {
    position: absolute;
    left: 0;
    width: 100%;
    text-align: center;
    transform: translateY(-50%);
    white-space: nowrap;
  }
  .brand-mark {
    position: absolute;
    left: 50%;
    top: 128px;
    width: 110px;
    height: 110px;
    transform: translate(-50%, -50%);
    border: 2px solid var(--copper);
    border-radius: 50%;
    box-sizing: border-box;
  }
  .wordmark {
    color: var(--copper);
    font-weight: 500;
    font-size: 50px;
    letter-spacing: 0.2em;
    text-indent: 0.2em;
    line-height: 1;
  }
  .card--generic .wordmark { top: 250px; }
  .card--founder .wordmark { top: 120px; }
  .social {
    position: absolute;
    left: 127px;
    display: flex;
    align-items: center;
    gap: 14px;
    transform: translateY(-50%);
    color: var(--blush);
    font-weight: 300;
    font-size: 23px;
    white-space: nowrap;
  }
  .social--instagram { top: 318px; }
  .social--facebook { top: 360px; }
  .social__icon {
    width: 29px;
    height: 29px;
    background: var(--blush);
    border-radius: 4px;
    flex: none;
  }
  .generic-contact {
    position: absolute;
    left: 0;
    width: 100%;
    top: 395px;
    margin: 0;
    padding: 0;
    list-style: none;
    text-align: center;
    color: var(--grey);
    font-weight: 400;
    font-size: 19px;
    line-height: 26px;
  }
  .person-name {
    top: 228px;
    color: var(--blush);
    font-weight: 500;
    font-size: 27px;
  }
  .person-title {
    top: 258px;
    color: var(--grey);
    font-weight: 400;
    font-size: 20px;
  }
  .divider {
    position: absolute;
    left: 50%;
    top: 291px;
    width: 172px;
    height: 1.5px;
    background: var(--copper);
    transform: translateX(-50%);
  }
  .contact {
    position: absolute;
    left: 0;
    width: 100%;
    top: 318px;
    margin: 0;
    padding: 0;
    list-style: none;
    text-align: center;
    color: var(--grey);
    font-weight: 400;
    font-size: 20px;
    line-height: 27px;
  }
</style>
</head>
<body>
<main class="canvas">
  <section class="card card--generic" aria-label="Generic business card">
    <div class="marble" role="img" aria-label="White marble texture"></div>
    <div class="brand-mark"></div>
    <div class="wordmark centered">QUIREMO</div>
    <div class="social social--instagram"><span class="social__icon"></span><span>quiremo_jewellery</span></div>
    <div class="social social--facebook"><span class="social__icon"></span><span>@quiremojewellery</span></div>
    <ul class="generic-contact">
      <li>+61436207518</li>
      <li>info@quiremo.com.au</li>
    </ul>
  </section>

  <section class="card card--founder" aria-label="Founder business card">
    <div class="marble" role="img" aria-label="White marble texture"></div>
    <div class="wordmark centered">QUIREMO</div>
    <div class="person-name centered">Sunela Parvaniya</div>
    <div class="person-title centered">Founder</div>
    <div class="divider"></div>
    <ul class="contact">
      <li>+61452913307</li>
      <li>sunela@quiremo.com.au</li>
      <li>www.quiremo.com.au</li>
      <li>ABN: 58219740312</li>
    </ul>
  </section>
</main>
</body>
</html>
```